Website for designing and selling name-labels

We are looking for a fresh design for a site similar to these (www.tovskrabe.no, www.dremsgard.no, www.kvalbuffo.no) where the consumer can come online designing their own labels (30x15 mm) , either with onlye text or with text, choose a pre-defined symbol (which we have) and/or a color. We will the print the labels on our side, and send it to the customer.

We are looking for the front page, product page and check out - page.

Target Market(s)

families with childring, scools, kinder garden, industry

Number of Pages Required

3 page

Requirements
Nice to have
• bright and easy design
easy to design and see their own designs
easy check out - few steps

```html
<!DOCTYPE html>
<html lang="en">
<head>
<meta charset="utf-8">
<title>Lappeklar – Name labels</title>
<link href="https://fonts.googleapis.com/css2?family=Luckiest+Guy&family=Rubik:wght@400;500;700&display=swap" rel="stylesheet">
<style>
:root{
  --teal:#1f9e95;
  --teal-dark:#17857d;
  --ink:#222;
  --muted:#666;
  --line:#e6e6e6;
  --footer:#333;
  --star:#f5b301;
  --sky:#bfe3ea;
  --sky2:#a9d9e2;
  --sun:#fbc14a;
  --sun-light:#fde2a6;
}
*{box-sizing:border-box;margin:0;padding:0}
html,body{width:1200px;height:3744px;overflow:hidden}
body{position:relative;font-family:"Rubik",sans-serif;color:var(--ink);background:#fff}
.abs{position:absolute}
.display{font-family:"Luckiest Guy",cursive}
a{color:inherit;text-decoration:none}

/* header */
.brand{left:112px;top:22px;display:flex;align-items:center;gap:10px;font-weight:700;font-size:26px;color:var(--teal);letter-spacing:1px}
.brand .sq{width:34px;height:34px;background:var(--teal)}
.contact{top:18px;display:flex;align-items:center;gap:12px}
.contact .ic{width:50px;height:50px;border:1.5px solid #ccc;border-radius:50%;display:flex;align-items:center;justify-content:center}
.contact small{display:block;color:var(--teal);font-size:14px}
.contact b{font-size:18px;font-weight:500}
.circle{width:50px;height:50px;border:1.5px solid #bbb;border-radius:50%}
.nav{top:105px;left:108px;right:108px;display:flex;justify-content:space-between;font-size:14px;letter-spacing:1px;color:#555}
.nav .on{color:var(--teal)}

/* hero */
.hero{left:0;top:141px;width:1200px;height:501px;background:linear-gradient(135deg,#8a93b5 0%,#b9bdd6 40%,#d9c7d3 70%,#6f7aa3 100%)}
.hero-title{left:273px;top:307px;width:654px;height:116px;background:rgba(31,158,149,.85);color:#fff;font-size:66px;display:flex;align-items:center;justify-content:center;letter-spacing:2px}
.btn-white{left:530px;top:452px;width:141px;height:43px;background:#fff;color:var(--teal);font-weight:500;font-size:16px;letter-spacing:1px;display:flex;align-items:center;justify-content:center}
.arrow{width:66px;height:66px;border-radius:50%;border:1.5px solid #333;display:flex;align-items:center;justify-content:center;background:#fff}
.arrow.light{border-color:#fff;background:transparent}

/* features */
.features{left:112px;top:728px;width:976px;height:177px;box-shadow:0 2px 10px rgba(0,0,0,.15);display:flex;background:#fff}
.feat{flex:1;text-align:center;padding-top:28px}
.feat h4{color:var(--teal);font-weight:500;font-size:17px;margin:16px 0 8px}
.feat p{font-size:13.5px;color:#555;letter-spacing:.5px}

/* section titles */
.sec-title{left:0;width:1200px;text-align:center;color:var(--teal);font-size:32px;letter-spacing:1px}
.sec-sub{left:0;width:1200px;text-align:center;font-size:14px;color:#333}

/* products */
.card{top:1092px;width:213px;height:274px;background:#fff;box-shadow:0 2px 8px rgba(0,0,0,.15);text-align:center}
.card.tall{height:320px}
.card .img{margin:14px auto 0;width:185px;height:160px}
.card h5{font-weight:500;font-size:17px;margin-top:12px}
.stars{color:var(--star);font-size:15px;margin-top:6px;letter-spacing:1px}
.stars span{color:#999}
.price{font-size:16px;margin-top:6px}
.price s{font-size:12px;color:#999;margin-left:8px}
.buy{margin:12px auto 0;width:199px;height:45px;border:1.5px solid var(--teal);color:var(--teal);display:flex;align-items:center;justify-content:center;font-weight:500;letter-spacing:1px}
.btn-teal{background:var(--teal);color:#fff;font-weight:500;display:flex;align-items:center;justify-content:center;letter-spacing:1px}

/* promos */
.promo{top:1584px;width:473px;height:400px;box-shadow:0 2px 8px rgba(0,0,0,.15);padding:50px 18px}
.promo h3{color:var(--teal);font-weight:500;font-size:20px}
.promo p{font-size:14px;margin-top:10px;line-height:1.5;width:270px}
.promo .btn-teal{width:200px;height:46px;margin-top:14px;font-size:18px}
.banner{left:15px;top:2079px;width:1185px;height:341px;background:linear-gradient(90deg,#fbf8f6 0%,#f3ece6 45%,#e2d3c5 75%,#d8e4ee 100%)}
.banner-copy{left:111px;top:2162px}
.banner-copy h3{color:var(--teal);font-weight:500;font-size:25px}
.banner-copy p{font-size:17px;line-height:1.5;margin-top:14px}
.banner-copy .btn-teal{width:246px;height:58px;margin-top:14px;font-size:20px}

/* testimonials */
.tcard{top:2605px;width:309px;height:260px;box-shadow:0 2px 8px rgba(0,0,0,.15);text-align:center;padding:30px 28px;background:#fff}
.tcard h4{color:var(--teal);font-weight:400;font-size:20px}
.tcard h6{font-weight:400;font-size:16px;margin-top:6px}
.tcard p{font-size:12.5px;color:#666;line-height:1.65;margin-top:12px}
.quote{right:18px;bottom:-16px;color:var(--teal);font-size:72px}

/* category grid */
.cat{display:flex;flex-direction:column;align-items:center;padding-top:14px;text-align:center}
.cat h4{font-weight:500;font-size:20px}
.cat p{font-size:12.5px;line-height:1.55;margin-top:6px;width:310px}
.cat .ghost{margin-top:10px;border:1.5px solid var(--teal);color:var(--teal);font-size:11.5px;letter-spacing:1px;width:140px;height:32px;display:flex;align-items:center;justify-content:center}

/* footer */
.footer{left:0;top:3325px;width:1200px;height:419px;background:var(--footer);color:#ddd}
.footer h5{font-weight:500;font-size:16px;letter-spacing:1px;color:#fff}
.footer ul{list-style:none;font-size:13px;line-height:25px;margin-top:14px}
.fbrand{left:112px;top:93px;font-weight:700;font-size:26px;color:var(--teal);display:flex;align-items:center;gap:10px;letter-spacing:1px}
.fbrand .sq{width:34px;height:34px;background:var(--teal)}
.fcircle{width:64px;height:64px;border:1.5px solid #999;border-radius:50%}
.input{left:745px;top:175px;width:342px;height:48px;background:#fff;color:#999;font-size:14px;padding:15px 30px}
.submit{left:745px;top:236px;width:147px;height:33px;font-size:14px}
.fline{left:112px;top:339px;width:976px;border-top:1px solid #555}
.fbottom{top:367px;font-size:13px;color:#ccc}
</style>
</head>
<body>

<!-- header -->
<div class="abs brand"><span class="sq"></span>LAPPEKLAR.NO</div>

<div class="abs contact" style="left:400px">
  <div class="ic"><svg width="22" height="22" viewBox="0 0 24 24" fill="none" stroke="#1f9e95" stroke-width="2"><path d="M5 3h4l2 5-2.5 1.5a11 11 0 0 0 6 6L16 13l5 2v4a2 2 0 0 1-2 2A16 16 0 0 1 3 5a2 2 0 0 1 2-2z"/></svg></div>
  <div><small>Call Us</small><b>400 12 345</b></div>
</div>
<div class="abs contact" style="left:622px">
  <div class="ic"><svg width="22" height="22" viewBox="0 0 24 24" fill="none" stroke="#1f9e95" stroke-width="2"><rect x="3" y="5" width="18" height="14"/><path d="M3 5l9 7 9-7"/></svg></div>
  <div><small>Email Us</small><b style="font-weight:400;font-size:17px">hei@lappeklar.no</b></div>
</div>
<svg class="abs" style="left:938px;top:28px" width="36" height="34" viewBox="0 0 36 34" fill="none" stroke="#1f9e95" stroke-width="2">
  <path d="M2 6h5l4 16h14l3-11H9"/><circle cx="13" cy="27" r="2"/><circle cx="23" cy="27" r="2"/>
  <circle cx="26" cy="8" r="7" fill="#222" stroke="none"/><text x="26" y="12" font-size="10" fill="#fff" stroke="none" text-anchor="middle" font-family="Rubik">2</text>
</svg>
<div class="abs circle" style="left:984px;top:18px" role="img" aria-label="Social profile"></div>
<div class="abs circle" style="left:1039px;top:18px" role="img" aria-label="Social profile"></div>

<nav class="abs nav">
  <a class="on">HOME</a><a>NAME TAGS</a><a>MINILAPPER</a><a>IRONING PADS</a><a>TEMALAPPER</a><a>MY ID</a><a>DRINKING BOTTLE</a><a>CONTACT US</a>
</nav>

<!-- hero -->
<div class="abs hero" role="img" aria-label="Children's dresses hanging on a clothes rail"></div>
<div class="abs hero-title display">KIDS COLLECTIONS</div>
<a class="abs btn-white">SHOP NOW</a>
<div class="abs arrow light" style="left:18px;top:356px"><svg width="16" height="16" viewBox="0 0 16 16" fill="none" stroke="#fff" stroke-width="2"><path d="M11 2L5 8l6 6"/></svg></div>
<div class="abs arrow light" style="left:1116px;top:356px"><svg width="16" height="16" viewBox="0 0 16 16" fill="none" stroke="#fff" stroke-width="2"><path d="M5 2l6 6-6 6"/></svg></div>

<!-- features -->
<div class="abs features">
  <div class="feat">
    <svg width="42" height="36" viewBox="0 0 42 36" fill="none" stroke="#333" stroke-width="2"><rect x="2" y="6" width="24" height="20"/><path d="M26 12h8l6 7v7H26"/><circle cx="10" cy="29" r="4" fill="#fff"/><circle cx="33" cy="29" r="4" fill="#fff"/></svg>
    <h4>FREE SHIPPING</h4><p>Free Shipping World Wide</p>
  </div>
  <div class="feat">
    <svg width="36" height="36" viewBox="0 0 36 36" fill="none" stroke="#333" stroke-width="2"><rect x="3" y="6" width="30" height="27"/><path d="M3 13h30M10 2v7M26 2v7"/><path d="M9 19h3M16 19h3M23 19h3M9 26h3M16 26h3M23 26h3"/></svg>
    <h4>MONEY BACK GUARANTEE</h4><p>100% Money Back Guarante</p>
  </div>
  <div class="feat">
    <svg width="36" height="36" viewBox="0 0 36 36" fill="none" stroke="#333" stroke-width="2"><rect x="4" y="8" width="28" height="22" rx="2"/><path d="M4 13l22-9 2 4"/><rect x="22" y="16" width="10" height="7"/></svg>
    <h4>ONLINE PAYMENT</h4><p>Contry To Popular Belief.</p>
  </div>
  <div class="feat">
    <svg width="36" height="36" viewBox="0 0 24 24" fill="none" stroke="#333" stroke-width="1.8"><path d="M5 3h4l2 5-2.5 1.5a11 11 0 0 0 6 6L16 13l5 2v4a2 2 0 0 1-2 2A16 16 0 0 1 3 5a2 2 0 0 1 2-2z"/><path d="M15 3a6 6 0 0 1 6 6M15 7a2 2 0 0 1 2 2"/></svg>
    <h4>HELP &amp; SUPPORT</h4><p>Call Us : 400 12 345</p>
  </div>
</div>

<!-- featured products -->
<h2 class="abs sec-title display" style="top:984px">FEATURED PRODUCTS</h2>
<p class="abs sec-sub" style="top:1034px">Shoppers like you are looking at these Products. Let’s take a look!</p>

<div class="abs arrow" style="left:18px;top:1196px"><svg width="16" height="16" viewBox="0 0 16 16" fill="none" stroke="#333" stroke-width="2"><path d="M11 2L5 8l6 6"/></svg></div>
<div class="abs arrow" style="left:1116px;top:1196px"><svg width="16" height="16" viewBox="0 0 16 16" fill="none" stroke="#333" stroke-width="2"><path d="M5 2l6 6-6 6"/></svg></div>

<div class="abs card" style="left:112px">
  <div class="img" role="img" aria-label="Baby lotion bottle" style="background:linear-gradient(180deg,#fff,#e7f2ef 40%,#fff)"></div>
  <h5>Snuggle Fleece Cozie</h5>
  <div class="stars">★★★★<span>★</span></div>
  <div class="price">$12.00<s>$18.00</s></div>
</div>
<div class="abs card tall" style="left:366px">
  <div class="img" role="img" aria-label="Light blue pencil case" style="background:radial-gradient(ellipse at center,#9fd3ea 0%,#cfe9f4 45%,#fff 70%)"></div>
  <h5>The Adventure Boy</h5>
  <div class="stars">★★★★<span>★</span></div>
  <div class="price">$12.00<s>$18.00</s></div>
  <a class="buy">BUY NOW</a>
</div>
<div class="abs card" style="left:620px">
  <div class="img" role="img" aria-label="Marker pen with blue cap" style="background:linear-gradient(160deg,#fafafa 30%,#d8dde8 50%,#fafafa 70%)"></div>
  <h5>It’s Friday Marker</h5>
  <div class="stars">★★★★<span>★</span></div>
  <div class="price">$12.00<s>$18.00</s></div>
</div>
<div class="abs card" style="left:875px">
  <div class="img" role="img" aria-label="Pair of scissors" style="background:linear-gradient(135deg,#fff 20%,#e9e4ee 45%,#f4d6cf 70%,#fff)"></div>
  <h5>Abstract Scissors</h5>
  <div class="stars">★★★★<span>★</span></div>
  <div class="price">$12.00<s>$18.00</s></div>
</div>

<a class="abs btn-teal" style="left:513px;top:1450px;width:199px;height:45px;font-size:17px">VIEW ALL</a>

<!-- promos -->
<div class="abs promo" style="left:112px;background:linear-gradient(160deg,#fafafa 0%,#f1f1f1 45%,#f6e9b8 65%,#f4c6d0 85%,#f0f0f0 100%)" role="img" aria-label="Baby bath products and towels">
  <h3>Perspiciatis unde omnis iste</h3>
  <p>Natus error sit voluptatem accusantium doloremque laudantium</p>
  <a class="btn-teal">SHOP NOW</a>
</div>
<div class="abs promo" style="left:615px;background:linear-gradient(135deg,#eaf5fa 0%,#dcecf3 40%,#f7b6d8 60%,#f6e46a 72%,#39bfc9 88%,#dbeef3 100%)" role="img" aria-label="Fan of colourful folders">
  <h3>Perspiciatis unde omnis iste</h3>
  <p>Natus error sit voluptatem accusantium doloremque laudantium</p>
  <a class="btn-teal">SHOP NOW</a>
</div>

<div class="abs banner" role="img" aria-label="Child walking through a bright nursery room"></div>
<div class="abs banner-copy">
  <h3>Perspiciatis unde omnis iste</h3>
  <p>Natus error sit voluptatem accusantium<br>doloremque laudantium</p>
  <a class="btn-teal">SHOP NOW</a>
</div>

<!-- testimonials -->
<h2 class="abs sec-title display" style="top:2498px">TESTIMONIALS</h2>
<p class="abs sec-sub" style="top:2549px">Satus error sit voluptatem accusantium doloremque laudantium</p>

<div class="abs arrow" style="left:18px;top:2703px"><svg width="16" height="16" viewBox="0 0 16 16" fill="none" stroke="#333" stroke-width="2"><path d="M11 2L5 8l6 6"/></svg></div>
<div class="abs arrow" style="left:1116px;top:2703px"><svg width="16" height="16" viewBox="0 0 16 16" fill="none" stroke="#333" stroke-width="2"><path d="M5 2l6 6-6 6"/></svg></div>

<div class="abs tcard" style="left:112px">
  <h4>Eirik T Solberg</h4><h6>Eioskn</h6>
  <p>Sed ut perspiciatis unde omnis iste natus error sit voluptatem accusantium doloremque laudantium, totam rem aperiam, eaque ipsa quae ab illo inventore veritatis et quasi architecto beatae vitae</p>
  <span class="abs quote display">”</span>
</div>
<div class="abs tcard" style="left:445px">
  <h4>Ingrid M Havik</h4><h6>Eioskn</h6>
  <p>Sed ut perspiciatis unde omnis iste natus error sit voluptatem accusantium doloremque laudantium, totam rem aperiam, eaque ipsa quae ab illo inventore veritatis et quasi architecto beatae vitae</p>
  <span class="abs quote display">”</span>
</div>
<div class="abs tcard" style="left:779px">
  <h4>Sunniva K Dahl</h4><h6>Eioskn</h6>
  <p>Sed ut perspiciatis unde omnis iste natus error sit voluptatem accusantium doloremque laudantium, totam rem aperiam, eaque ipsa quae ab illo inventore veritatis et quasi architecto beatae vitae</p>
  <span class="abs quote display">”</span>
</div>

<!-- categories -->
<div class="abs" style="left:112px;top:2946px;width:534px;height:147px;background:var(--sky)">
  <div class="abs" style="left:10px;top:70px;width:220px;height:75px;background:linear-gradient(90deg,#c9525a,#4a6a9a,#e6a04a,#7c9a4a)" role="img" aria-label="Assorted sports balls"></div>
  <div class="cat abs" style="left:170px;top:0;width:340px"><h4>Sports Equipment</h4><p>Sed ut perspiciatis unde omnis iste natus error sit voluptatem accusantium doloremque.</p><a class="ghost">SHOP NOW</a></div>
</div>
<div class="abs" style="left:646px;top:2946px;width:442px;height:147px;background:var(--sky2)">
  <div class="abs" style="left:280px;top:8px;width:150px;height:132px;background:linear-gradient(135deg,#555,#8a7a5a 50%,#c9b04a)" role="img" aria-label="Tool belt with hand tools"></div>
  <div class="cat abs" style="left:0;top:0;width:260px"><h4>Tool</h4><p style="width:220px">Sed ut perspiciatis unde omnis iste natus error sit.</p><a class="ghost">SHOP NOW</a></div>
</div>
<div class="abs" style="left:112px;top:3093px;width:468px;height:150px;background:var(--sun-light)">
  <div class="abs" style="left:15px;top:14px;width:130px;height:136px;background:linear-gradient(180deg,#9a8a6a,#3a3a30)" role="img" aria-label="Walking cane"></div>
  <div class="cat abs" style="left:130px;top:0;width:330px"><h4>Retirement Homes</h4><p>Sed ut perspiciatis unde omnis iste natus error sit voluptatem accusantium doloremque.</p><a class="ghost">SHOP NOW</a></div>
</div>
<div class="abs" style="left:580px;top:3093px;width:508px;height:150px;background:var(--sun)">
  <div class="abs" style="left:340px;top:18px;width:140px;height:120px;background:radial-gradient(ellipse,#f6d23a 40%,#f3b42e 70%)" role="img" aria-label="Yellow school backpack"></div>
  <div class="cat abs" style="left:0;top:0;width:360px"><h4>Kindergarten and school</h4><p>Sed ut perspiciatis unde omnis iste natus error sit voluptatem accusantium doloremque.</p><a class="ghost">SHOP NOW</a></div>
</div>

<!-- footer -->
<footer class="abs footer">
  <div class="abs fbrand"><span class="sq"></span>LAPPEKLAR.NO</div>
  <div class="abs fcircle" style="left:142px;top:211px" role="img" aria-label="Social profile"></div>
  <div class="abs fcircle" style="left:219px;top:211px" role="img" aria-label="Social profile"></div>

  <div class="abs" style="left:418px;top:67px">
    <h5>QUICK LINKS</h5>
    <ul><li>Home</li><li>Name tags</li><li>Minilapper</li><li>Ironing pads</li><li>Temalapper</li><li>MY ID</li><li>Drinking bottle</li><li>Contact Us</li></ul>
  </div>
  <div class="abs" style="left:590px;top:67px">
    <h5>LINKS</h5>
    <ul><li>Terms &amp; Condition</li><li>Privacy Policy</li><li>Sitemap</li></ul>
  </div>
  <div class="abs" style="left:745px;top:67px">
    <h5>GET OUR LATEST UPDATES</h5>
    <p style="font-size:13px;line-height:26px;margin-top:14px">Enter your mail and we'll send you all uptodate<br>latest blog and news</p>
  </div>
  <div class="abs input">Enter your mail</div>
  <a class="abs btn-teal submit">SUBMIT</a>

  <div class="abs fline"></div>
  <p class="abs fbottom" style="left:112px">Copyrights ©2021. All Rights Reserved</p>
  <p class="abs fbottom" style="left:875px">Privacy Policy</p>
  <div class="abs" style="left:975px;top:359px;height:30px;border-left:1px solid #666"></div>
  <p class="abs fbottom" style="left:998px">Terms and Use</p>
</footer>

</body>
</html>
```